Membership Based Medical Practice Website

We need a functioning website for a new Membership based medical practice. There will be an enrollment fee and a monthly fee. We would like to see designs that are modern, simple. Should use neutral light colors. Examples of sites we like are www.kellanmoorclinic.com and https://fernholtcare.com/ We also have a link that when "Join Now" is clicked it will go to the signup website.

Target Market(s)

Gay Men, local population, Age group 20 to 60's.

Industry/Entity Type

Medical

Coding

Coded - Design and coding required

Number of Pages Required

5+ page

Font styles to use
Sans Serif

Colors
ffffff
cee9f5
ecf7fb
cfeae6
edf8f6
aaaaaa
e9e9e9
dbdbdb
fff3d1

Requirements
Must have
• Logo and header on every page. Clean, simple design, clear content, mobile compatible.
• Must use Wordpress
Nice to have
• Ideas should come from kellanmoorclinic.com
• Easy to read
Should not have
• Generic patient pictures, bold colors.
• Should not copy from above websites.

```html
<!DOCTYPE html>
<html lang="en">
<head>
<meta charset="utf-8">
<title>Lakeshore Infectious Disease Specialists</title>
<link href="https://fonts.googleapis.com/css2?family=Montserrat:wght@400;500;600;700&family=Open+Sans:wght@400;600&display=swap" rel="stylesheet">
<style>
:root{
  --white:#ffffff;
  --sky:#cee9f5;
  --sky-soft:#ecf7fb;
  --mint:#cfeae6;
  --mint-soft:#edf8f6;
  --grey:#aaaaaa;
  --grey-light:#e9e9e9;
  --grey-mid:#dbdbdb;
  --cream:#fff3d1;
  --ink:#2b2b2b;
  --text:#444444;
  --gold:#c9a24a;
  --footer:#333333;
  --icon:#5a6b73;
}
*{box-sizing:border-box;margin:0;padding:0}
html,body{width:1200px;height:3358px;overflow:hidden}
body{position:relative;background:var(--white);font-family:"Open Sans",Arial,sans-serif;color:var(--text)}
.abs{position:absolute}

/* hero */
.hero{left:0;top:0;width:1200px;height:615px;background:linear-gradient(180deg,#e8eaec 0%,#d4d8da 35%,#9aa39a 58%,#4d5a40 75%,#2f3232 100%)}
.hero-notch{left:540px;top:614px}
.brand{left:142px;top:150px;width:290px;text-align:center;font-family:"Montserrat",Arial,sans-serif;color:var(--ink)}
.brand-name{font-size:21px;letter-spacing:14px;font-weight:400}
.brand-sub{font-size:15px;letter-spacing:0.5px;margin-top:2px}
.brand-mark{left:262px;top:40px;width:50px;height:50px;border-radius:50%;border:2px solid var(--gold)}
.nav{top:20px;left:520px;display:flex;align-items:center;gap:0;font-family:"Open Sans",Arial,sans-serif;font-size:13.5px;color:#333}
.nav a{color:#333;text-decoration:none;margin:0 14px}
.nav a.active{color:var(--gold)}
.nav .join{background:var(--mint);border-radius:18px;padding:7px 18px;margin-left:8px;margin-right:0}
.hero-title{left:0;top:270px;width:1200px;text-align:center;font-family:"Montserrat",Arial,sans-serif;font-size:25px;line-height:37px;color:#3a3a3a}

/* expertise */
.sec-title{left:0;width:1200px;text-align:center;font-family:"Montserrat",Arial,sans-serif;font-size:26px;color:var(--ink);font-weight:400}
.expertise{left:145px;top:777px;width:455px;height:439px;background:var(--mint-soft);padding:38px 22px}
.expertise h3{font-family:"Montserrat",Arial,sans-serif;font-weight:400;font-size:16px;color:var(--ink);margin-bottom:18px}
.expertise li{list-style:none;font-size:13px;line-height:36.8px;color:#333}
.expertise li::before{content:"›";margin-right:14px;font-size:16px}
.expertise-photo{left:600px;top:777px;width:455px;height:439px;background:linear-gradient(180deg,#b9a7a6 0%,#d7b58a 45%,#e9b65c 62%,#6a4a2a 100%)}

/* features */
.features-bg{left:0;top:1295px;width:1200px;height:1023px;background:var(--sky-soft)}
.notch-up{left:540px;top:1275px}
.feature{width:300px}
.feature .disc{width:118px;height:118px;border-radius:50%;background:var(--sky);display:flex;align-items:center;justify-content:center}
.feature h4{font-family:"Montserrat",Arial,sans-serif;font-weight:400;font-size:16px;color:var(--ink);margin:22px 0 6px}
.feature p{font-size:11px;line-height:16px;color:#555}
.notch-down{left:540px;top:2317px}

/* pricing */
.plan-band{left:145px;top:2474px;width:910px;height:78px;background:var(--cream);display:flex;align-items:center;justify-content:center;font-family:"Montserrat",Arial,sans-serif;font-weight:700;font-size:25px;color:#4a4a4a}
.plan-photo{left:145px;top:2552px;width:455px;height:443px;background:radial-gradient(circle at 45% 50%,#e8e6e2 0%,#c9c8c4 22%,#8a2a28 45%,#3a3f4a 80%)}
.plan-perks{left:600px;top:2552px;width:455px;height:443px;background:var(--grey-light);padding:36px 35px}
.plan-perks li{list-style:none;font-size:13.5px;line-height:19px;color:#333;margin-bottom:16px;padding-left:20px;position:relative}
.plan-perks li::before{content:"›";position:absolute;left:0;font-size:16px}
.cta{left:477px;top:3077px;width:246px;height:56px;border-radius:28px;background:var(--mint);display:flex;align-items:center;justify-content:center;font-family:"Montserrat",Arial,sans-serif;font-size:17px;color:#333;text-decoration:none}

/* footer */
.footer{left:0;top:3213px;width:1200px;height:145px;background:var(--footer)}
.footer-notch{left:550px;top:3212px}
.footer-links{left:145px;top:3270px;font-size:11px;color:#ddd}
.footer-links a{color:#ddd;text-decoration:none}
.footer-links span{margin:0 8px}
.copyright{left:145px;top:3304px;font-size:11px;color:#bbb}
.social{top:3287px;display:flex;gap:20px;left:964px}
.social i{display:block;width:14px;height:14px;border-radius:50%;background:#bbb}
</style>
</head>
<body>

<div class="abs hero" role="img" aria-label="Photograph of a straight country road leading into misty green mountains"></div>
<svg class="abs hero-notch" width="120" height="26" viewBox="0 0 120 26"><path d="M0 0 H120 L60 26 Z" fill="#2f3232"/><path d="M50 4 L60 12 L70 4" fill="none" stroke="#fff" stroke-width="3"/></svg>

<div class="abs brand-mark" aria-hidden="true"></div>
<div class="abs brand">
  <div class="brand-name">LAKESHORE</div>
  <div class="brand-sub">INFECTIOUS DISEASE SPECIALISTS</div>
</div>

<nav class="abs nav">
  <a class="active" href="#">Home</a>
  <a href="#">Specialties</a>
  <a href="#">Pricing</a>
  <a href="#">About Us</a>
  <a href="#">FAQ</a>
  <a href="#">Blog</a>
  <a class="join" href="#">Join Us</a>
</nav>

<h1 class="abs hero-title" style="font-weight:400">Specialty medicine with<br>Commitment, Compassion and Care</h1>

<h2 class="abs sec-title" style="top:728px">We offer comprehensive treatment of a wide variety of infectious diseases.</h2>

<div class="abs expertise">
  <h3>Out expertise is in the following area.</h3>
  <ul>
    <li>HIV/PrEP</li>
    <li>Chronic Hepatitis</li>
    <li>Sexually transmitted infections</li>
    <li>Pre-travel vaccinations and counselling</li>
    <li>Infections associated with medical devices</li>
    <li>Bone and Joint infections</li>
    <li>Postsurgical infections</li>
    <li>Diabetes related infections</li>
    <li>Tuberculosis</li>
  </ul>
</div>
<div class="abs expertise-photo" role="img" aria-label="Photograph of four friends embracing, seen from behind, at sunset"></div>

<div class="abs features-bg"></div>
<svg class="abs notch-up" width="120" height="21" viewBox="0 0 120 21"><path d="M0 21 L60 0 L120 21 Z" fill="#ecf7fb"/></svg>
<h2 class="abs sec-title" style="top:1393px;line-height:40px">Less wait, more personal.<br>We are not your traditional doctor’s office.</h2>

<div class="abs feature" style="left:145px;top:1520px">
  <div class="disc"><svg width="60" height="60" viewBox="0 0 60 60" fill="none" stroke="#5a6b73" stroke-width="2"><rect x="22" y="10" width="22" height="36" rx="2"/><rect x="14" y="22" width="22" height="26" rx="2"/><text x="33" y="33" font-size="12" fill="#5a6b73" stroke="none" text-anchor="middle">$</text></svg></div>
  <h4>Straightforward pricing</h4>
  <p>We charge all our patients the same low rate - no surprises.</p>
</div>
<div class="abs feature" style="left:455px;top:1520px">
  <div class="disc"><svg width="60" height="60" viewBox="0 0 60 60" fill="none" stroke="#5a6b73" stroke-width="2"><rect x="8" y="12" width="44" height="38" rx="2"/><line x1="8" y1="22" x2="52" y2="22"/><path d="M16 30h4M26 30h4M36 30h4M16 38h4M26 38h4M36 38h4" /><path d="M18 8v8M42 8v8"/></svg></div>
  <h4>Available when you are</h4>
  <p>New patient appointments are available within 1 week.</p>
</div>
<div class="abs feature" style="left:765px;top:1520px">
  <div class="disc"><svg width="60" height="60" viewBox="0 0 60 60" fill="none" stroke="#5a6b73" stroke-width="2"><rect x="12" y="8" width="30" height="42" rx="2"/><circle cx="27" cy="20" r="5"/><path d="M18 32h18M18 38h14"/><path d="M48 20 L36 46 L34 50 L38 47 L50 22 Z"/></svg></div>
  <h4>Hassle-free booking</h4>
  <p>Schedule your appointment online at your convenience - no need to call during business hours.</p>
</div>

<div class="abs feature" style="left:145px;top:1765px">
  <div class="disc"><svg width="60" height="60" viewBox="0 0 60 60" fill="none" stroke="#5a6b73" stroke-width="2"><path d="M22 10h30v22H34l-6 6v-6h-6z"/><path d="M8 22h22v20H18l-6 6v-6H8z"/><path d="M13 30h12M13 36h9"/></svg></div>
  <h4>Devoted care</h4>
  <p>We schedule enough time at each visit to make sure all of your questions are answered.</p>
</div>
<div class="abs feature" style="left:455px;top:1765px">
  <div class="disc"><svg width="60" height="60" viewBox="0 0 60 60" fill="none" stroke="#5a6b73" stroke-width="2"><rect x="16" y="6" width="26" height="48" rx="3"/><circle cx="29" cy="24" r="5"/><path d="M21 38c2-6 14-6 16 0"/><rect x="34" y="12" width="18" height="12" rx="1"/><line x1="26" y1="49" x2="32" y2="49"/></svg></div>
  <h4>Within your reach</h4>
  <p>Follow-up appointments may be done by video chat for your convenience.</p>
</div>
<div class="abs feature" style="left:765px;top:1765px">
  <div class="disc"><svg width="60" height="60" viewBox="0 0 60 60" fill="none" stroke="#5a6b73" stroke-width="2"><rect x="26" y="8" width="8" height="24" rx="1" transform="rotate(-25 30 20)"/><path d="M14 50h34M20 50c0-10 6-14 14-14"/><circle cx="18" cy="30" r="6"/><path d="M36 40h10"/></svg></div>
  <h4>Save on lab costs</h4>
  <p>If paying upfront for labs, we offer discounted pricing of up to 90% off standard rates.</p>
</div>

<div class="abs feature" style="left:145px;top:2008px">
  <div class="disc"><svg width="60" height="60" viewBox="0 0 60 60" fill="none" stroke="#5a6b73" stroke-width="2"><rect x="20" y="8" width="20" height="8" rx="1"/><rect x="18" y="16" width="24" height="36" rx="2"/><path d="M30 26v14M23 33h14"/></svg></div>
  <h4>Save on medications</h4>
  <p>We offer deeply discounted wholesale price medications for our members at pharmacy on site.</p>
</div>
<div class="abs feature" style="left:455px;top:2008px">
  <div class="disc"><svg width="60" height="60" viewBox="0 0 60 60" fill="none" stroke="#5a6b73" stroke-width="2"><path d="M6 26l10-10 8 6 8-4 8 4 8-6 6 10"/><path d="M16 30l12 12c2 2 5 2 6 0l12-12"/><path d="M24 30l8 8M30 28l6 6"/></svg></div>
  <h4>No middle man</h4>
  <p>We don’t bill any insurance plans so decisions about your healthcare will be made by you and Dr. Halvorsen, without the impersonal management that comes from third-party payers.</p>
</div>

<svg class="abs notch-down" width="120" height="21" viewBox="0 0 120 21"><path d="M0 0 L60 21 L120 0 Z" fill="#ecf7fb"/></svg>

<h2 class="abs sec-title" style="top:2415px">Our pricing is simple, transparent and affordable.</h2>
<div class="abs plan-band">MEMBERSHIP PLAN $80/MO, PLUS A ONE-TIME $99 ENROLLMENT FEE.</div>
<div class="abs plan-photo" role="img" aria-label="Photograph of a person in a red sweater holding an enamel mug filled with snow"></div>
<ul class="abs plan-perks">
  <li>Includes all appointments, no co-pay</li>
  <li>Relaxed, unrushed visits</li>
  <li>Direct communication with your doctor via phone, email, video chat 24/7</li>
  <li>Convenient online scheduling (no need to call during business hours)</li>
  <li>Wholesale price for labs and medications</li>
</ul>

<a class="abs cta" href="#">Learn more about us</a>

<div class="abs footer"></div>
<svg class="abs footer-notch" width="100" height="20" viewBox="0 0 100 20"><path d="M0 0 L50 20 L100 0 Z" fill="#ffffff"/></svg>
<div class="abs footer-links"><a href="#">Home</a><span>|</span><a href="#">Specialties</a><span>|</span><a href="#">Pricing</a><span>|</span><a href="#">About Us</a><span>|</span><a href="#">FAQ</a><span>|</span><a href="#">Blog</a><span>|</span><a href="#">Join Us</a></div>
<div class="abs copyright">Copyright © 2019 &nbsp;Lakeshore Infectious Disease Specialists. &nbsp; All rights reserved.</div>
<div class="abs social" aria-label="Social links"><i></i><i></i><i></i></div>

</body>
</html>
```